Retail/Wholesale website graphic template

I need to design a new graphic template for a website for a client. The website will be a retail/wholesale company site with most pages dedicated to presentation. There will also be an online store and a blog. However, you don't need to worry about those. All I need from you is a graphic template for a generic site page.

It will need to include standard UI elements, in case I need those. I am attaching a more detailed assignment in .docx format.

The logo is also attached.

Target Market(s)

small business owners, (occasional) retail customers

Industry/Entity Type

Wholesale

Number of Pages Required

1 page

Font styles to use
Serif
Sans Serif

Colors
ec1f27
474747

Requirements
Must have
• must match logo, be clean, minimal and with slightly larger text size
Should not have
• must not be modern-looking where you have to scroll and scroll and scroll to get to the bottom of the homepage. most of my visitors are "old" people, they do not get this type of design.

```html
<!DOCTYPE html>
<html lang="en">
<head>
<meta charset="utf-8">
<title>Corvane Imports</title>
<link href="https://fonts.googleapis.com/css2?family=Questrial&family=Open+Sans:wght@400;600;700&display=swap" rel="stylesheet">
<style>
:root{
  --red:#ec1f27;
  --dark:#474747;
  --nav:#3d3d3d;
  --footer:#3f3f3f;
  --ink:#222;
  --text:#444;
  --muted:#666;
  --band:#eceff2;
  --line:#d9d9d9;
  --white:#fff;
  --hero-a:#0b3f86;
  --hero-b:#2f78d0;
  --hero-c:#9fc6f0;
}
*{box-sizing:border-box;margin:0;padding:0}
html,body{width:1200px;height:2786px;overflow:hidden;background:var(--white)}
body{font-family:"Open Sans",Arial,sans-serif;color:var(--text);position:relative}
.display{font-family:"Questrial","Century Gothic",sans-serif;font-weight:400}
section,header,nav,footer{position:absolute;left:0;width:1200px}

/* header */
.site-header{top:0;height:97px}
.brand{position:absolute;left:108px;top:30px;height:40px;display:flex;align-items:center;gap:12px}
.brand-mark{width:18px;height:18px;background:var(--red)}
.brand-name{font-family:"Questrial",sans-serif;font-size:30px;line-height:1;color:var(--dark);white-space:nowrap}
.contact{position:absolute;top:40px;display:flex;align-items:center;gap:10px;font-size:19px;color:var(--dark);white-space:nowrap}
.contact.phone{left:660px}
.contact.mail{left:838px}
.contact-sep{position:absolute;left:818px;top:38px;width:1px;height:30px;background:var(--line)}

/* nav */
.main-nav{top:97px;height:41px;background:var(--nav)}
.main-nav ul{list-style:none;display:flex;height:41px;padding-left:100px}
.main-nav li{height:41px;display:flex;align-items:center;padding:0 28px;color:var(--white);font-size:15px;border-right:1px solid #555;gap:6px}
.main-nav li:last-child{border-right:0}
.main-nav li.active{color:var(--red)}
.caret{width:10px;height:6px}

/* hero */
.hero{top:138px;height:518px;background:linear-gradient(120deg,var(--hero-c) 0%,var(--hero-b) 35%,var(--hero-a) 70%,#06295c 100%)}
.hero-title{position:absolute;left:108px;top:124px;width:640px;color:var(--white);font-size:28px;line-height:54px;font-family:"Questrial",sans-serif;font-weight:400}
.hero-arrow{position:absolute;top:242px;width:34px;height:34px;background:#2a2a2a;display:flex;align-items:center;justify-content:center}
.hero-arrow.prev{left:8px}
.hero-arrow.next{right:8px}

/* intro */
.intro{top:656px;height:362px}
.intro-copy{position:absolute;left:108px;top:60px;width:624px}
.intro-copy h2{font-size:35px;color:var(--ink);margin-bottom:28px}
.intro-lead{font-size:13.5px;line-height:24px;color:var(--ink);font-weight:600;margin-bottom:12px}
.intro-body{font-size:12.5px;line-height:24px;color:var(--text)}
.advantages{position:absolute;left:786px;top:59px;width:323px;height:266px;background:#f4f4f4;border:1px solid #e2e2e2}
.adv-head{height:43px;background:var(--dark);display:flex;align-items:center;padding-left:10px;gap:10px}
.adv-brand{color:var(--white);font-family:"Questrial",sans-serif;font-size:22px}
.adv-title{color:var(--red);font-family:"Questrial",sans-serif;font-size:22px}
.adv-lead{font-size:12.5px;font-weight:700;color:var(--ink);line-height:20px;padding:10px 6px 6px}
.adv-list{list-style:none;padding:0 6px}
.adv-list li{font-size:12.5px;line-height:25px;color:var(--text);padding-left:16px;position:relative}
.adv-list li::before{content:"";position:absolute;left:0;top:10px;width:6px;height:6px;border-radius:50%;background:var(--red)}

/* help band */
.help{top:1018px;height:251px;background:var(--band);text-align:center}
.help h2{font-size:39px;color:var(--ink);margin-top:37px}
.help p{font-size:22px;line-height:33px;color:#111;width:900px;margin:12px auto 0}
.btn{display:inline-block;background:var(--red);color:var(--white);font-size:17px;line-height:39px;padding:0 12px;border-radius:2px}
.help .btn{margin-top:16px}

/* news */
.news{top:1269px;height:734px;text-align:center}
.news h2{font-size:37px;color:var(--ink);margin-top:56px}
.cards{position:absolute;left:108px;top:158px;display:flex;gap:9px}
.card{width:327px;height:440px;border:1px solid var(--line);background:var(--white);text-align:left;padding:6px}
.card-media{width:313px;height:229px}
.media-a{background:linear-gradient(135deg,#f0f0f0,#7d7d7d 60%,#2b2b2b)}
.media-b{background:linear-gradient(135deg,#c9c6bd,#5b6773 55%,#2d3540)}
.media-c{background:linear-gradient(160deg,#8f979b,#c8bda8 60%,#a99a80)}
.tag{display:inline-block;margin-top:15px;font-size:10.5px;color:var(--white);line-height:26px;padding:0 10px;background:var(--dark);text-transform:uppercase;font-weight:600}
.tag.red{background:var(--red)}
.card h3{font-size:17.5px;font-weight:600;color:var(--ink);margin-top:13px}
.card .byline{font-size:11.5px;color:var(--muted);margin-top:7px}
.card .excerpt{font-size:11.5px;line-height:22px;color:var(--text);margin-top:10px}
.news .btn{position:absolute;left:554px;top:633px;padding:0 14px}

/* clients */
.clients{top:2003px;height:236px;background:var(--band);text-align:center}
.clients h2{font-size:34px;color:var(--ink);margin-top:44px}
.client-row{position:absolute;left:106px;top:122px;display:flex;gap:12px}
.client{width:133px;height:62px;background:var(--white);border:1px solid #dcdcdc;display:flex;align-items:center;justify-content:center;gap:6px;font-size:15px;font-weight:700;color:#222;white-space:nowrap}
.client-dot{width:14px;height:14px;border-radius:50%;background:#222}
.client-arrow{position:absolute;top:140px;width:18px;height:30px}
.client-arrow.prev{left:56px}
.client-arrow.next{right:56px}

/* callback */
.callback{top:2239px;height:489px;background:linear-gradient(90deg,#f3f3f3 0%,#fafafa 45%,#ffffff 100%)}
.callback-media{position:absolute;left:0;top:0;width:483px;height:489px;background:linear-gradient(150deg,#fbfbfb 20%,#d8d8d8 60%,#eeeeee 90%)}
.callback-form{position:absolute;left:506px;top:48px;width:635px}
.callback-form h2{display:inline-block;font-size:31px;color:#222;letter-spacing:0.5px;padding:0 10px 10px;border-bottom:1px solid #ddd;white-space:nowrap}
.fields{display:grid;grid-template-columns:300px 300px;column-gap:35px;margin-top:24px}
.field{font-size:12.5px;color:#555;height:59px;border-bottom:1px solid #ccc;padding-top:8px}
.field.wide{grid-column:1/3;border:0;height:auto;padding-top:18px}
.textarea{margin-top:10px;height:87px;border:1px solid #ccc;background:rgba(255,255,255,.6)}
.submit{display:inline-block;margin-top:16px;background:var(--red);color:var(--white);font-weight:700;font-size:15px;line-height:38px;padding:0 26px;letter-spacing:.5px}

/* footer */
.site-footer{top:2728px;height:58px;background:var(--footer);display:flex;align-items:center}
.copyright{margin-left:108px;font-size:14px;color:#e5e5e5}
.social{position:absolute;left:878px;top:12px;display:flex;gap:8px;list-style:none}
.social li{width:34px;height:34px;border-radius:50%;background:#6e6e6e}
</style>
</head>
<body>

<header class="site-header">
  <div class="brand"><span class="brand-mark"></span><span class="brand-name">Corvane Imports</span></div>
  <div class="contact phone">
    <svg width="18" height="20" viewBox="0 0 18 20"><path d="M4 1 L7 1 L8 6 L6 8 C7 11 9 13 11 14 L13 12 L17 13 L17 17 C10 18 2 11 3 2 Z" fill="none" stroke="#ec1f27" stroke-width="1.8"/></svg>
    <span>555.014.2736</span>
  </div>
  <span class="contact-sep"></span>
  <div class="contact mail">
    <svg width="28" height="20" viewBox="0 0 28 20"><rect x="1" y="1" width="26" height="18" fill="none" stroke="#ec1f27" stroke-width="2"/><path d="M1 1 L14 11 L27 1" fill="none" stroke="#ec1f27" stroke-width="2"/></svg>
    <span>hello@corvaneimports.example</span>
  </div>
</header>

<nav class="main-nav">
  <ul>
    <li class="active">Home</li>
    <li>Products <svg class="caret" viewBox="0 0 10 6"><path d="M0 0 L5 6 L10 0" fill="none" stroke="#ec1f27" stroke-width="2"/></svg></li>
    <li>Solutions <svg class="caret" viewBox="0 0 10 6"><path d="M0 0 L5 6 L10 0" fill="none" stroke="#ec1f27" stroke-width="2"/></svg></li>
    <li>Support</li>
    <li>Free Trial</li>
    <li>About</li>
    <li>Login</li>
  </ul>
</nav>

<section class="hero" role="img" aria-label="Global shipping scene with cargo ship, containers, crane, airplane and globe over a world map">
  <h1 class="hero-title">Lorem Ipsum Dolor Sit Amet, Consectetuer Adipiscing Elit, Sed Diam Nonummy.</h1>
  <span class="hero-arrow prev"><svg width="10" height="14" viewBox="0 0 10 14"><path d="M8 1 L2 7 L8 13" fill="none" stroke="#fff" stroke-width="2.5"/></svg></span>
  <span class="hero-arrow next"><svg width="10" height="14" viewBox="0 0 10 14"><path d="M2 1 L8 7 L2 13" fill="none" stroke="#fff" stroke-width="2.5"/></svg></span>
</section>

<section class="intro">
  <div class="intro-copy">
    <h2 class="display">A World with Many Screens ...</h2>
    <p class="intro-lead">Lorem ipsum dolor sit amet, consectetuer adipiscing elit, sed diam nonummy nibh euismod tincidunt ut laoreet dolore magna aliquam erat volutpat.</p>
    <p class="intro-body">Lorem ipsum dolor sit amet, consectetuer adipiscing elit, sed diam nonummy nibh euismod tincidunt ut laoreet dolore magna aliquam erat volutpat. Ut wisi enim ad minim veniam, quis nostrud exerci tation ullamcorper suscipit lobortis nisl ut aliquip ex ea commodo consequat. Duis autem vel eum iriure dolor in hendrerit in vulputate velit esse molestie consequat, vel illum dolore eu feugiat nulla facilisis at vero eros et accumsan et iusto odio dignissim qui blandit praesent luptatum zzril delenit augue duis facilisi.</p>
  </div>
  <aside class="advantages">
    <div class="adv-head"><span class="adv-brand">Corvane</span><span class="adv-title">Advantages</span></div>
    <p class="adv-lead">Lorem ipsum dolor sit amet, consectetue adipiscing elit, sed diam nonummy nibh euismod.</p>
    <ul class="adv-list">
      <li>Aadipiscing elit, sed diam nonummy nibh</li>
      <li>Aadipiscing elit, sed dia</li>
      <li>Aadipiscing elit, sed diam nonummy</li>
      <li>Aadipiscing elit, sed diam nonummy nibh</li>
      <li>Aadipiscing elit, sed diam no</li>
      <li>Aadipiscing elit, sed diam nonummy</li>
    </ul>
  </aside>
</section>

<section class="help">
  <h2 class="display">We Are Here To Help You</h2>
  <p>Lorem ipsum dolor sit amet, consectetuer adipiscing elit, sed diam nonummy nibh euismod tincidunt ut laoreet</p>
  <span class="btn">Get A Free Trail</span>
</section>

<section class="news">
  <h2 class="display">Recent News and Blog</h2>
  <div class="cards">
    <article class="card">
      <div class="card-media media-a" role="img" aria-label="Hands working with a calculator and magnifying glass over paperwork"></div>
      <span class="tag red">Lorem ipsumsd</span>
      <h3>Lorem ipsum dolor consectetue</h3>
      <p class="byline">By: Simply Dummy Text</p>
      <p class="excerpt">Lorem ipsum dolor sit amete, consectetuer adipiscing elit, sed diam nonummy nibh euismod tincidunt utlaor dolore ma aliquam erat volutpat...[+]</p>
    </article>
    <article class="card">
      <div class="card-media media-b" role="img" aria-label="Person working at a desktop computer in an office"></div>
      <span class="tag">Lorem ips</span>
      <h3>Lorem ipsum dolor consectetuer</h3>
      <p class="byline">By: Simply Dummy Text</p>
      <p class="excerpt">Lorem ipsum dolor sit amete, consectetuer adipiscing elit, sed diam nonummy nibh euismod tincidunt utlaor dolore ma aliquam erat volutpat...[+]</p>
    </article>
    <article class="card">
      <div class="card-media media-c" role="img" aria-label="Folded paper fortune teller resting in beach grass and sand"></div>
      <span class="tag">Lorem ipsumsd</span>
      <h3>Lorem ipum dolor consectetuer</h3>
      <p class="byline">By: Simply Dummy Text</p>
      <p class="excerpt">Lorem ipsum dolor sit amete, consectetuer adipiscing elit, sed diam nonummy nibh euismod tincidunt utlaor dolore ma aliquam erat volutpat...[+]</p>
    </article>
  </div>
  <span class="btn">View All</span>
</section>

<section class="clients">
  <h2 class="display">Our Clients</h2>
  <svg class="client-arrow prev" viewBox="0 0 18 30"><path d="M16 2 L3 15 L16 28" fill="none" stroke="#b5b5b5" stroke-width="2"/></svg>
  <div class="client-row">
    <div class="client"><span class="client-dot"></span>Altamere</div>
    <div class="client"><span class="client-dot"></span>Brightmoor</div>
    <div class="client">Tessline</div>
    <div class="client">Quadra Works</div>
    <div class="client"><span class="client-dot"></span>Altamere</div>
    <div class="client">Lumacrest</div>
    <div class="client"><span class="client-dot"></span>Brightmoor</div>
  </div>
  <svg class="client-arrow next" viewBox="0 0 18 30"><path d="M2 2 L15 15 L2 28" fill="none" stroke="#b5b5b5" stroke-width="2"/></svg>
</section>

<section class="callback">
  <div class="callback-media" role="img" aria-label="Hands typing on a laptop beside a coffee cup and small plant on a white desk"></div>
  <div class="callback-form">
    <h2 class="display">REQUEST A CALL BACK</h2>
    <div class="fields">
      <div class="field">First Name</div>
      <div class="field">Last Name</div>
      <div class="field">Email</div>
      <div class="field">Phone Number</div>
      <div class="field wide">Details About Your Enquiry<div class="textarea"></div></div>
    </div>
    <span class="submit">SUBMIT</span>
  </div>
</section>

<footer class="site-footer">
  <p class="copyright">Copyright © 2018 Corvane Imports. All Rights Reserved.</p>
  <ul class="social" aria-label="Social links">
    <li></li><li></li><li></li><li></li><li></li>
  </ul>
</footer>

</body>
</html>
```